Business Card Design for Flood Rescue 360 - Property Restoration Professionals

I need a business card designed for Flood Rescue 360. We are a full-service property restoration solution. Providing water, fire, smoke & storm restoration as well as mold remediation and full remodel or reconstruction to homes and businesses across Dallas-Fort Worth, TX.
Target Market(s)
home and business owners with insurance covered property damage from water, fire or storm related damage
Industry/Entity Type
property restoration
Contact Information for Business Card
Marcus Pelley General Manager Cell: 214-555-0193 Office: 469-555-0148 email: Marcus@FloodRescue360.example services: Water, Fire, Mold, Reconstruction Tagline: Urgency for Your Water Emergency!
Look and feel
Each slider illustrates characteristics of the customer's brand and the style your logo design should communicate.

```html
<!DOCTYPE html>
<html lang="en">
<head>
<meta charset="utf-8">
<title>Flood Rescue 360 – Business Card</title>
<link rel="stylesheet" href="https://fonts.googleapis.com/css2?family=Montserrat:wght@400;500;800;900&display=swap">
<style>
  :root {
    --backdrop: #4b4b4b;
    --card: #161616;
    --card-edge: #1d1d1d;
    --brand-blue: #12a9e2;
    --text-light: #f2f2f2;
    --pattern-dark: #0e0e0e;
    --pattern-mid: #2a2a2a;
  }
  * { box-sizing: border-box; margin: 0; padding: 0; }
  html, body { width: 1200px; height: 801px; overflow: hidden; }
  body {
    background: var(--backdrop);
    font-family: "Montserrat", sans-serif;
    color: var(--text-light);
    position: relative;
  }
  .card {
    position: absolute;
    top: 246px;
    width: 540px;
    height: 309px;
    background: var(--card);
    border-bottom: 3px solid var(--brand-blue);
    overflow: hidden;
  }
  .card-front { left: 40px; }
  .card-back { left: 620px; }

  /* Front */
  .brand {
    position: absolute;
    left: 34px; top: 30px;
    display: flex; align-items: center; gap: 12px;
  }
  .brand-mark {
    width: 44px; height: 44px; border-radius: 50%;
    border: 3px solid var(--brand-blue);
  }
  .brand-name {
    font-weight: 900; font-size: 27px; line-height: 0.95;
    text-transform: uppercase; color: var(--brand-blue);
  }
  .person { position: absolute; left: 34px; top: 110px; }
  .person-name { font-weight: 800; font-size: 25px; color: var(--brand-blue); }
  .person-title { font-weight: 400; font-size: 14px; margin-top: 2px; }
  .tagline { position: absolute; left: 34px; top: 176px; font-size: 13px; }
  .contacts { position: absolute; left: 34px; top: 204px; list-style: none; }
  .contacts li {
    display: flex; align-items: center; gap: 8px;
    font-size: 13px; line-height: 20px;
  }
  .contacts svg { width: 12px; height: 12px; flex: none; }

  .services { position: absolute; right: 30px; top: 34px; text-align: right; }
  .services-heading {
    font-weight: 900; font-size: 25px; letter-spacing: 0.5px;
    text-transform: uppercase; color: var(--brand-blue); margin-bottom: 6px;
  }
  .services ul { list-style: none; }
  .services li {
    display: flex; justify-content: flex-end; align-items: center; gap: 7px;
    font-size: 14px; line-height: 22px;
  }
  .service-dot {
    width: 8px; height: 8px; border-radius: 50%;
    border: 1.5px solid var(--brand-blue);
  }

  /* Back */
  .back-texture {
    position: absolute; inset: 0;
    background: linear-gradient(115deg, var(--pattern-mid) 0%, #1c1c1c 40%, var(--pattern-dark) 100%);
  }
  .back-brand {
    position: absolute; right: 110px; top: 135px;
    display: flex; align-items: center; gap: 8px;
  }
  .back-brand .brand-mark { width: 22px; height: 22px; border-width: 2px; }
  .back-brand .brand-name { font-size: 14px; line-height: 1; }
</style>
</head>
<body>
  <section class="card card-front" aria-label="Business card front">
    <div class="brand">
      <span class="brand-mark"></span>
      <div class="brand-name">Flood<br>Rescue 360</div>
    </div>

    <div class="person">
      <div class="person-name">Marcus Pelley</div>
      <div class="person-title">General Manager</div>
    </div>

    <p class="tagline">Urgency for Your Water Emergency!</p>

    <ul class="contacts">
      <li>
        <svg viewBox="0 0 12 12"><rect x="3" y="0.8" width="6" height="10.4" rx="1" fill="none" stroke="#12a9e2" stroke-width="1.3"/></svg>
        214-555-0193
      </li>
      <li>
        <svg viewBox="0 0 12 12"><path d="M1 4 Q6 0 11 4 L9.5 5.5 L8 4.5 Q6 3.8 4 4.5 L2.5 5.5 Z M3 6 H9 L10 11 H2 Z" fill="#12a9e2"/></svg>
        469-555-0148
      </li>
      <li>
        <svg viewBox="0 0 12 12"><rect x="0.8" y="2.5" width="10.4" height="7" fill="none" stroke="#12a9e2" stroke-width="1.3"/><path d="M1 3 L6 7 L11 3" fill="none" stroke="#12a9e2" stroke-width="1.3"/></svg>
        Marcus@FloodRescue360.example
      </li>
      <li>
        <svg viewBox="0 0 12 12"><circle cx="6" cy="6" r="5" fill="none" stroke="#12a9e2" stroke-width="1.3"/><path d="M1 6 H11 M6 1 Q3 6 6 11 M6 1 Q9 6 6 11" fill="none" stroke="#12a9e2" stroke-width="1"/></svg>
        FloodRescue360.example
      </li>
    </ul>

    <div class="services">
      <h2 class="services-heading">Services</h2>
      <ul>
        <li>Water <span class="service-dot"></span></li>
        <li>Fire <span class="service-dot"></span></li>
        <li>Mold <span class="service-dot"></span></li>
        <li>Reconstruction <span class="service-dot"></span></li>
      </ul>
    </div>
  </section>

  <section class="card card-back" aria-label="Business card back">
    <div class="back-texture" role="img" aria-label="Repeating embossed brand symbol pattern in dark and silver tones"></div>
    <div class="back-brand">
      <span class="brand-mark"></span>
      <span class="brand-name">Flood Rescue 360</span>
    </div>
  </section>
</body>
</html>
```